Venture 482 - Lumora Book Cover

I am looking for a Lumora book cover for my book about "Venture 482".
The Book is Titled:
Venture 482 Ascended
Shaping Outcomes: Paths To Unlocking Cosmic Truths
Author is Dorian Pell
Here is a book description that may help you understand more about it:
Inspired by the genius of Edwin Marlowe, this comprehensive guide delves into the ancient wisdom and cutting-edge science behind the 482 method, a powerful tool for manifesting your desires. Whether you're seeking personal growth, financial success, or spiritual enlightenment, this book provides advanced techniques and methods to transform your dreams into reality.
Any questions please ask.
Thanks
Owen

```html
<!DOCTYPE html>
<html lang="en">
<head>
<meta charset="utf-8">
<title>Venture 482 Ascended — Dorian Pell</title>
<link rel="stylesheet" href="https://fonts.googleapis.com/css2?family=Cormorant+Garamond:wght@500&family=Italianno&family=Source+Sans+3:wght@700&display=swap">
<style>
  :root {
    --backdrop: #262626;
    --cover-black: #000000;
    --ink-white: #ffffff;
    --ink-lilac: #d3dcff;
    --nebula-violet: #6a4bd6;
    --nebula-blue: #4f72e8;
    --nebula-glow: #c9d6ff;
  }
  * { margin: 0; padding: 0; box-sizing: border-box; }
  html, body {
    width: 1200px;
    height: 1200px;
    overflow: hidden;
    background: var(--backdrop);
  }
  .cover {
    position: absolute;
    left: 219px;
    top: 29px;
    width: 761px;
    height: 1142px;
    background: var(--cover-black);
    overflow: hidden;
  }
  .cover__nebula {
    position: absolute;
    inset: 0;
    width: 100%;
    height: 100%;
  }
  .cover__series {
    position: absolute;
    top: 84px;
    left: 0;
    width: 100%;
    text-align: center;
    font-family: "Cormorant Garamond", serif;
    font-weight: 500;
    font-size: 33px;
    letter-spacing: 4px;
    line-height: 1;
    color: var(--ink-white);
  }
  .cover__title {
    position: absolute;
    left: 30px;
    top: 300px;
    display: flex;
    align-items: baseline;
    white-space: nowrap;
    font-weight: normal;
  }
  .cover__title-script {
    font-family: "Italianno", cursive;
    font-size: 200px;
    line-height: 1;
    color: var(--ink-lilac);
  }
  .cover__title-block {
    position: relative;
    top: 52px;
    margin-left: 10px;
    font-family: "Source Sans 3", sans-serif;
    font-weight: 700;
    font-size: 50px;
    line-height: 1;
    letter-spacing: 1px;
    color: var(--ink-lilac);
  }
  .cover__subtitle {
    position: absolute;
    right: 68px;
    top: 913px;
    text-align: right;
    font-family: "Cormorant Garamond", serif;
    font-weight: 500;
    font-size: 33px;
    line-height: 43px;
    letter-spacing: 3px;
    color: var(--ink-white);
  }
  .cover__author {
    position: absolute;
    right: 72px;
    top: 1030px;
    font-family: "Cormorant Garamond", serif;
    font-weight: 500;
    font-size: 42px;
    line-height: 1;
    letter-spacing: 5px;
    color: var(--ink-white);
  }
</style>
</head>
<body>
  <main class="cover">
    <svg class="cover__nebula" viewBox="0 0 761 1142" role="img" aria-label="Glowing violet and blue cosmic nebula streaming diagonally across a starry night sky">
      <defs>
        <radialGradient id="nebula-band" cx="50%" cy="50%" r="50%">
          <stop offset="0%" stop-color="var(--nebula-glow)" stop-opacity="0.75"/>
          <stop offset="35%" stop-color="var(--nebula-blue)" stop-opacity="0.65"/>
          <stop offset="70%" stop-color="var(--nebula-violet)" stop-opacity="0.35"/>
          <stop offset="100%" stop-color="var(--nebula-violet)" stop-opacity="0"/>
        </radialGradient>
        <radialGradient id="nebula-haze" cx="50%" cy="50%" r="50%">
          <stop offset="0%" stop-color="var(--nebula-violet)" stop-opacity="0.5"/>
          <stop offset="100%" stop-color="var(--nebula-violet)" stop-opacity="0"/>
        </radialGradient>
      </defs>
      <ellipse cx="400" cy="620" rx="640" ry="250" transform="rotate(-30 400 620)" fill="url(#nebula-haze)"/>
      <ellipse cx="380" cy="640" rx="580" ry="160" transform="rotate(-30 380 640)" fill="url(#nebula-band)"/>
    </svg>

    <p class="cover__series">VENTURE 482 ASCENDED</p>
    <h1 class="cover__title">
      <span class="cover__title-script">Shaping</span>
      <span class="cover__title-block">OUTCOMES</span>
    </h1>
    <p class="cover__subtitle">PATHS TO UNLOCKING<br>COSMIC TRUTHS</p>
    <p class="cover__author">Dorian Pell</p>
  </main>
</body>
</html>
```